Layout for site fence advertising - length approx. 250 cm x 125 cm

The advertising will later be printed on a PVC film and used for events or on sports fields.

Main services :
Your regional contact at
Real estate and business financing
independent insurance advice

```html
<!DOCTYPE html>
<html lang="en">
<head>
<meta charset="utf-8">
<title>RM Finanzberatung – Fence Banner</title>
<link href="https://fonts.googleapis.com/css2?family=Lexend:wght@400;500&family=Montserrat:wght@600;700;800&display=swap" rel="stylesheet">
<style>
  :root {
    --brand-blue: #1f4fb8;
    --band-blue: #1b4fbf;
    --band-deep: #0f2f86;
    --tab-gray: #6b6b6b;
    --text-gray: #4a4a4a;
    --light-1: #f7f7f7;
    --light-2: #e6e7ea;
    --stage: #e4e4e4;
    --white: #ffffff;
  }
  * { margin: 0; padding: 0; box-sizing: border-box; }
  html, body { width: 972px; height: 1200px; overflow: hidden; }
  body { background: var(--stage); position: relative; }

  .banner {
    position: absolute; left: 36px; top: 375px;
    width: 900px; height: 450px; overflow: hidden;
    background: linear-gradient(125deg, var(--light-1) 0%, var(--light-2) 45%, var(--light-1) 70%, var(--light-2) 100%);
    box-shadow: 0 4px 14px rgba(0,0,0,.25);
  }

  .brand-ring {
    position: absolute; left: 46px; top: 24px;
    width: 160px; height: 160px; border-radius: 50%;
    border: 5px solid var(--brand-blue);
  }
  .brand-divider {
    position: absolute; left: 225px; top: 24px;
    width: 4px; height: 165px; background: var(--text-gray);
  }
  .brand-name {
    position: absolute; left: 240px; top: 68px;
    font-family: "Lexend", sans-serif; font-weight: 500;
    font-size: 31px; color: var(--brand-blue); white-space: nowrap;
  }
  .brand-tagline {
    position: absolute; left: 240px; top: 112px;
    font-family: "Lexend", sans-serif; font-weight: 400;
    font-size: 21px; color: var(--text-gray); white-space: nowrap;
  }

  .faint-ring {
    position: absolute; left: 500px; top: 146px;
    width: 180px; height: 180px; border-radius: 50%;
    border: 5px solid rgba(31,79,184,.12);
  }

  .portrait {
    position: absolute; right: 0; top: 0;
    width: 240px; height: 288px;
    background: linear-gradient(180deg, #d9b8a4 0%, #c99d87 45%, #2d2d38 70%, #22222c 100%);
  }

  .region-tab {
    position: absolute; left: 0; top: 245px; width: 430px; height: 43px;
  }
  .region-tab span {
    position: absolute; left: 24px; top: 5px;
    font-family: "Montserrat", sans-serif; font-weight: 700;
    font-size: 25px; color: var(--white); white-space: nowrap;
  }

  .service-band { position: absolute; left: 0; top: 288px; width: 900px; height: 162px; }

  .service {
    position: absolute; top: 288px; text-align: center;
    font-family: "Montserrat", sans-serif; font-weight: 700;
    color: var(--white); font-size: 20px; line-height: 1.35;
  }
  .service-financing { left: 20px; width: 260px; }
  .service-insurance { left: 330px; width: 280px; }
  .service-icon {
    display: block; margin: 14px auto 8px;
    width: 52px; height: 52px;
  }
  .service-financing .service-label { margin-top: 2px; }
  .service-insurance .service-label { margin-top: 4px; }

  .contact {
    position: absolute; left: 660px; top: 288px; width: 240px;
    font-family: "Montserrat", sans-serif; color: var(--white); text-align: center;
  }
  .contact-heading { margin-top: 32px; font-weight: 700; font-size: 17px; }
  .contact-rule { display: block; margin: 4px auto 0; width: 132px; height: 4px; }
  .contact-phone {
    margin-top: 8px; font-weight: 800; font-size: 24px; white-space: nowrap;
    display: flex; align-items: center; justify-content: center; gap: 5px;
  }
  .contact-web {
    margin-top: 2px; font-weight: 600; font-size: 17px; white-space: nowrap;
    display: flex; align-items: center; justify-content: center; gap: 6px;
  }
  .contact-web b { font-weight: 800; }
</style>
</head>
<body>
  <div class="banner">
    <div class="brand-ring"></div>
    <div class="brand-divider"></div>
    <div class="brand-name">RM Finanzberatung GmbH</div>
    <div class="brand-tagline">Finanzieren, Versichern, Vorsorgen</div>

    <div class="faint-ring"></div>

    <div class="portrait" role="img" aria-label="Portrait photo of the advisor in a dark suit and white shirt"></div>

    <svg class="region-tab" viewBox="0 0 430 43" aria-hidden="true">
      <polygon points="0,0 395,0 430,43 0,43" fill="var(--tab-gray)"/>
    </svg>
    <div class="region-tab"><span>Your regional contact at</span></div>

    <svg class="service-band" viewBox="0 0 900 162" preserveAspectRatio="none" aria-hidden="true">
      <defs>
        <linearGradient id="bandLeft" x1="0" y1="0" x2="1" y2="1">
          <stop offset="0" stop-color="#1d55c6"/><stop offset="1" stop-color="#143d9c"/>
        </linearGradient>
        <linearGradient id="bandMid" x1="0" y1="0" x2="1" y2="1">
          <stop offset="0" stop-color="#1e58cc"/><stop offset="1" stop-color="#12378f"/>
        </linearGradient>
        <linearGradient id="bandRight" x1="0" y1="0" x2="1" y2="1">
          <stop offset="0" stop-color="#1b50bf"/><stop offset="1" stop-color="#0f2f86"/>
        </linearGradient>
      </defs>
      <polygon points="0,0 325,0 282,162 0,162" fill="url(#bandLeft)"/>
      <polygon points="325,0 680,0 595,162 282,162" fill="url(#bandMid)"/>
      <polygon points="680,0 900,0 900,162 595,162" fill="url(#bandRight)"/>
    </svg>

    <div class="service service-financing">
      <svg class="service-icon" viewBox="0 0 52 52" aria-hidden="true">
        <circle cx="26" cy="26" r="24" fill="var(--white)" stroke="#9fb7ea" stroke-width="2"/>
        <path d="M16 25 L26 16 L36 25 M19 23 V34 H33 V23" fill="none" stroke="var(--brand-blue)" stroke-width="2" stroke-linejoin="round"/>
        <rect x="23" y="27" width="6" height="7" fill="none" stroke="var(--brand-blue)" stroke-width="2"/>
      </svg>
      <div class="service-label">Real estate and<br>Business financing</div>
    </div>

    <div class="service service-insurance">
      <svg class="service-icon" viewBox="0 0 52 52" aria-hidden="true">
        <circle cx="26" cy="26" r="24" fill="var(--white)" stroke="#9fb7ea" stroke-width="2"/>
        <rect x="15" y="16" width="22" height="16" rx="2" fill="none" stroke="var(--brand-blue)" stroke-width="2"/>
        <path d="M20 32 L18 37 L24 32" fill="none" stroke="var(--brand-blue)" stroke-width="2" stroke-linejoin="round"/>
        <path d="M26 19 L31 21 V24 C31 27 29 29 26 30 C23 29 21 27 21 24 V21 Z" fill="none" stroke="var(--brand-blue)" stroke-width="1.6"/>
        <path d="M23.5 24 L25.5 26 L28.5 22.5" fill="none" stroke="var(--brand-blue)" stroke-width="1.6"/>
      </svg>
      <div class="service-label">Independent<br>Insurance advice</div>
    </div>

    <div class="contact">
      <div class="contact-heading">Call Us Today:</div>
      <svg class="contact-rule" viewBox="0 0 132 4" aria-hidden="true">
        <rect x="0" y="1.5" width="132" height="1" fill="rgba(255,255,255,.7)"/>
        <rect x="50" y="0" width="32" height="4" rx="2" fill="var(--white)"/>
      </svg>
      <div class="contact-phone">
        <svg width="18" height="18" viewBox="0 0 18 18" aria-hidden="true">
          <circle cx="9" cy="9" r="8" fill="none" stroke="var(--white)" stroke-width="2"/>
          <path d="M6 5 L8 7 L7 8 C7.5 9.5 8.5 10.5 10 11 L11 10 L13 12 L12 13.5 C8 13 5 10 4.5 6 Z" fill="var(--white)"/>
        </svg>
        0123 555 0198
      </div>
      <div class="contact-web">
        <svg width="15" height="15" viewBox="0 0 16 16" aria-hidden="true">
          <circle cx="8" cy="8" r="7" fill="none" stroke="var(--white)" stroke-width="1.4"/>
          <ellipse cx="8" cy="8" rx="3" ry="7" fill="none" stroke="var(--white)" stroke-width="1.2"/>
          <path d="M1 8 H15 M2.5 4.5 H13.5 M2.5 11.5 H13.5" stroke="var(--white)" stroke-width="1.2"/>
        </svg>
        <span>www.<b>website</b>.com</span>
      </div>
    </div>
  </div>
</body>
</html>
```